BRIGHT RIVER POWER.

I'd like my business logo.
contact name: Dennis Halvorsen
phone:0438759164
email: info@brightriverpower.net.au
website: www.brightriverpower.net.au

services:
solar
battery storage
LED lighting
energy saving solutions
general electrical
I'd like the design to look professional

Target Market(s)

Everyone

Industry/Entity Type

Business

Contact Information for Business Card

as described above

Requirements
Must have
• Id like the colours and the design to work well with my logo.

```html
<!DOCTYPE html>
<html lang="en">
<head>
<meta charset="utf-8">
<title>Bright River Power – Business Card</title>
<link href="https://fonts.googleapis.com/css2?family=Open+Sans:wght@400;600;700&display=swap" rel="stylesheet">
<style>
  :root {
    --page-bg: #e9eaea;
    --card-white: #ffffff;
    --brand-green: #4ea83a;
    --green-light: #a3cf3b;
    --green-deep: #3f9f35;
    --sun-orange: #f6a21a;
    --text-grey: #4a4a4a;
    --rule-grey: #8c8c8c;
    --white: #ffffff;
  }
  * { box-sizing: border-box; margin: 0; padding: 0; }
  html, body {
    width: 1105px; height: 1200px; overflow: hidden;
    background: var(--page-bg);
    font-family: "Open Sans", Arial, sans-serif;
  }
  .card {
    position: absolute;
    left: 193px;
    width: 720px;
    height: 410px;
    overflow: hidden;
  }
  /* Front */
  .card--front { top: 167px; background: var(--card-white); }
  .brand-lockup {
    position: absolute; right: 36px; top: 84px;
    display: flex; align-items: center; gap: 14px;
  }
  .brand-lockup__dot {
    width: 26px; height: 26px; border-radius: 50%;
    background: var(--sun-orange);
  }
  .brand-lockup__name {
    font-size: 34px; font-weight: 600; color: var(--brand-green);
    letter-spacing: -0.3px; white-space: nowrap;
  }
  .contact-name {
    position: absolute; left: 37px; top: 290px;
    font-size: 24px; font-weight: 600; color: var(--brand-green);
  }
  .contact-rule {
    position: absolute; left: 37px; right: 37px; top: 331px;
    border-top: 1px solid var(--rule-grey);
  }
  .contact-list {
    position: absolute; left: 37px; right: 20px; top: 346px;
    display: flex; gap: 10px; list-style: none;
    font-size: 14.5px; color: var(--text-grey); white-space: nowrap;
  }
  .contact-list li { display: flex; align-items: center; gap: 5px; }
  .contact-list svg { width: 15px; height: 15px; fill: var(--brand-green); flex: none; }
  /* Back */
  .card--back {
    top: 623px;
    background: radial-gradient(ellipse 70% 90% at 48% 40%, var(--green-light) 0%, #72b93a 45%, var(--green-deep) 100%);
  }
  .decor-area {
    position: absolute; left: 330px; top: 0; width: 390px; height: 410px;
    background: radial-gradient(circle at 62% 52%, rgba(255,255,255,0.16) 0%, rgba(255,255,255,0.07) 45%, rgba(255,255,255,0) 72%);
  }
  .service-list {
    position: absolute; left: 48px; top: 111px;
    list-style: none; color: var(--white);
    font-size: 19px; line-height: 28px;
  }
  .service-list li::before {
    content: ""; display: inline-block;
    width: 7px; height: 7px; border-radius: 50%;
    background: var(--white); margin-right: 12px; vertical-align: middle;
    position: relative; top: -2px;
  }
  .brand-name--back {
    position: absolute; left: 41px; top: 272px;
    font-size: 42px; font-weight: 600; color: var(--white);
    letter-spacing: -0.5px; white-space: nowrap;
  }
</style>
</head>
<body>
  <section class="card card--front">
    <div class="brand-lockup">
      <span class="brand-lockup__dot"></span>
      <span class="brand-lockup__name">Bright River Power</span>
    </div>
    <h1 class="contact-name">Dennis Halvorsen</h1>
    <div class="contact-rule"></div>
    <ul class="contact-list">
      <li>
        <svg viewBox="0 0 24 24" aria-hidden="true"><path d="M6.6 10.8a15.1 15.1 0 0 0 6.6 6.6l2.2-2.2c.3-.3.7-.4 1-.2 1.1.4 2.3.6 3.6.6.6 0 1 .4 1 1V20c0 .6-.4 1-1 1A17 17 0 0 1 3 4c0-.6.4-1 1-1h3.5c.6 0 1 .4 1 1 0 1.3.2 2.5.6 3.6.1.3 0 .7-.2 1z"/></svg>
        0438759164
      </li>
      <li>
        <svg viewBox="0 0 24 24" aria-hidden="true"><path d="M2 5h20v14H2zm2 2v.5l8 5 8-5V7l-8 5z"/></svg>
        info@brightriverpower.net.au
      </li>
      <li>
        <svg viewBox="0 0 24 24" aria-hidden="true"><path d="M12 2a10 10 0 1 0 0 20 10 10 0 0 0 0-20zm-1 17.9A8 8 0 0 1 4.2 10L9 14.8v1a2 2 0 0 0 2 2zm6.9-2.5A2 2 0 0 0 16 16h-1v-3a1 1 0 0 0-1-1H8v-2h2a1 1 0 0 0 1-1V7h2a2 2 0 0 0 2-2v-.4a8 8 0 0 1 2.9 12.8z"/></svg>
        brightriverpower.net.au
      </li>
    </ul>
  </section>

  <section class="card card--back">
    <div class="decor-area" role="img" aria-label="Faint large brand emblem decoration"></div>
    <ul class="service-list">
      <li>Solar</li>
      <li>Battery storage</li>
      <li>LED lighting</li>
      <li>Energy saving solutions</li>
    </ul>
    <div class="brand-name--back">Bright River Power</div>
  </section>
</body>
</html>
```